FinTech company looking to revamp and expand client-facing interface for our financial models

Pellworth Engines currently has a very simple website that allows clients to interact with our financial models. We are looking to completely redesign the current site and add several extra pages to provide extra functionality. We want the design to have a modern, slick feel, that will work on both a desktop or a tablet. It should be straightforward for clients to move between different pages at any time, and clear from the layout how to interact with the more advanced features. We have included screenshots of existing pages in the attached design brief, as well as sketches of the functionality required by the new pages, but can't provide a direct link to the current site.
Target Market(s)
Professional investors that will be paying to access the interface
Industry/Entity Type
Finance
Number of Pages Required
4 page
Colors
Designer to choose colors to be used in the design.
Look and feel
Each slider illustrates characteristics of the customer's brand and the style your logo design should communicate.

```html
<!DOCTYPE html>
<html lang="en">
<head>
<meta charset="utf-8">
<title>Pellworth – Models</title>
<link rel="stylesheet" href="https://fonts.googleapis.com/css2?family=Roboto:wght@400;500;700&family=Roboto+Condensed:wght@400&family=Open+Sans:wght@400;600;700&display=swap">
<style>
  :root {
    --backdrop: #e6e6e6;
    --page: #f7f7f7;
    --nav-top: #1a2f8c;
    --nav-bottom: #00043a;
    --nav-active: #4b4b4b;
    --nav-models: #1f1f1f;
    --nav-divider: #3a4aa0;
    --rule-navy: #0b0f5c;
    --tab-text: #444;
    --header-top: #3a3a3a;
    --header-bottom: #111;
    --cell-border: #d9d9d9;
    --text: #111;
    --accent: #1a3f9a;
    --white: #fff;
  }
  * { box-sizing: border-box; margin: 0; padding: 0; }
  html, body { width: 1200px; height: 757px; overflow: hidden; }
  body { background: var(--backdrop); font-family: "Roboto", Arial, sans-serif; color: var(--text); position: relative; }

  .page { position: absolute; left: 14px; top: 14px; width: 1172px; height: 729px; background: var(--page); }

  .topbar { position: absolute; left: 0; top: 0; width: 100%; height: 55px;
    background: linear-gradient(var(--nav-top), var(--nav-bottom)); display: flex; color: var(--white); }
  .brand { width: 166px; display: flex; align-items: center; padding-left: 40px; font-family: "Open Sans", Arial, sans-serif; font-weight: 600; font-size: 16px; }
  .period { width: 83px; display: flex; align-items: center; justify-content: center; font-weight: 700; font-size: 13px;
    border-right: 1px solid var(--nav-divider); }
  .period.is-active { background: var(--nav-active); }
  .spacer { flex: 1; }
  .mainnav { display: flex; align-items: center; gap: 8px; font-weight: 700; font-size: 12.5px; padding: 0 14px; }
  .mainnav svg { width: 20px; height: 20px; }
  .mainnav.models { width: 130px; background: var(--nav-models); justify-content: center; }
  .mainnav.sens { width: 164px; justify-content: center; border-right: 1px solid var(--nav-divider); }
  .mainnav.favs { width: 182px; justify-content: center; }

  .navy-rule { position: absolute; left: 0; top: 101px; width: 100%; height: 3px; background: var(--rule-navy); }
  .tabband { position: absolute; left: 0; top: 104px; width: 100%; height: 62px;
    background: linear-gradient(#fdfdfd, #dcdcdc); }
  .tabs { position: absolute; left: 219px; top: 116px; display: flex; gap: 5px; }
  .tab { width: 143px; height: 51px; background: linear-gradient(#f4f4f4, #e9e9e9); border-radius: 4px 4px 0 0;
    display: flex; flex-direction: column; align-items: center; justify-content: center; gap: 4px;
    font-family: "Open Sans", Arial, sans-serif; font-weight: 600; font-size: 12.5px; color: var(--tab-text); }
  .tab svg { width: 18px; height: 18px; }

  .filters { position: absolute; left: 53px; top: 203px; font-family: "Open Sans", Arial, sans-serif; font-size: 15px; }
  .filter-row { position: relative; height: 28px; margin-bottom: 9px; }
  .filter-name { position: absolute; left: 0; top: 4px; }
  .filter-key { position: absolute; left: 79px; top: 4px; font-weight: 700; }
  .filter-name b { font-weight: 700; }
  .filter-input { position: absolute; left: 173px; top: 0; width: 166px; height: 28px; border: 2px solid #ddd; border-radius: 4px; background: var(--white);
    padding-left: 10px; font-size: 15px; display: flex; align-items: center; }

  .export { position: absolute; right: 52px; top: 244px; display: flex; align-items: center; gap: 8px;
    color: var(--accent); font-family: "Open Sans", Arial, sans-serif; font-weight: 700; font-size: 16px; }
  .export svg { width: 24px; height: 22px; }

  .models-table { position: absolute; left: 51px; top: 295px; width: 1070px; border-collapse: collapse;
    font-family: "Roboto Condensed", "Arial Narrow", sans-serif; font-size: 15px; background: var(--white);
    border-radius: 6px; overflow: hidden; }
  .models-table th { height: 65px; background: linear-gradient(var(--header-top), var(--header-bottom)); color: var(--white);
    font-family: "Open Sans", Arial, sans-serif; font-weight: 600; font-size: 15.5px; border-right: 1px solid #555; }
  .models-table th svg { width: 10px; height: 7px; margin-left: 5px; vertical-align: middle; }
  .models-table th:last-child, .models-table td:last-child { border-right: none; }
  .models-table td { height: 65px; border-right: 1px solid var(--cell-border); border-bottom: 1px solid var(--cell-border);
    padding-left: 8px; line-height: 1.3; }
  .models-table tr:last-child td { border-bottom: none; }
  .models-table td.id, .models-table td.time, .models-table td.quality { text-align: center; padding-left: 0; }
</style>
</head>
<body>
<div class="page">
  <header class="topbar">
    <div class="brand">Pellworth</div>
    <div class="period is-active">250D</div>
    <div class="period">83D</div>
    <div class="period">42D</div>
    <div class="spacer"></div>
    <div class="mainnav models">
      <svg viewBox="0 0 24 24" fill="#fff"><path d="M12 3 2 12h3v9h5v-6h4v6h5v-9h3z"/></svg>MODELS
    </div>
    <div class="mainnav sens">
      <svg viewBox="0 0 24 24" fill="#fff"><circle cx="12" cy="3" r="1.6"/><circle cx="12" cy="21" r="1.6"/><circle cx="3" cy="12" r="1.6"/><circle cx="21" cy="12" r="1.6"/><circle cx="5.6" cy="5.6" r="1.6"/><circle cx="18.4" cy="18.4" r="1.6"/><circle cx="5.6" cy="18.4" r="1.6"/><circle cx="18.4" cy="5.6" r="1.6"/><circle cx="12" cy="8" r="1.3"/><circle cx="12" cy="16" r="1.3"/><circle cx="8" cy="12" r="1.3"/><circle cx="16" cy="12" r="1.3"/></svg>SENSITIVITIES
    </div>
    <div class="mainnav favs">
      <svg viewBox="0 0 24 24" fill="none" stroke="#fff" stroke-width="1.8"><path d="M12 2.5l2.9 6.2 6.6.7-5 4.5 1.4 6.6L12 17.2l-5.9 3.3 1.4-6.6-5-4.5 6.6-.7z"/></svg>FAVOURITES
    </div>
  </header>

  <div class="navy-rule"></div>
  <div class="tabband"></div>
  <nav class="tabs">
    <div class="tab"><svg viewBox="0 0 18 18" fill="#444"><rect x="1" y="3" width="16" height="2"/><rect x="1" y="8" width="12" height="2"/><rect x="14" y="8" width="3" height="2"/><rect x="1" y="13" width="16" height="2"/></svg>EQUITIES</div>
    <div class="tab"><svg viewBox="0 0 18 18" fill="#444"><rect x="2" y="11" width="3" height="6"/><rect x="7" y="8" width="3" height="9"/><rect x="12" y="5" width="3" height="12"/><path d="M2 8l5-4 4 3 5-5" stroke="#444" stroke-width="1.5" fill="none"/></svg>ETFS</div>
    <div class="tab"><svg viewBox="0 0 18 18" fill="none" stroke="#444" stroke-width="1.6"><circle cx="8" cy="10" r="6.5"/><circle cx="8" cy="10" r="3"/><path d="M8 10l8-8M13 2h3v3"/></svg>PAIRS</div>
    <div class="tab"><svg viewBox="0 0 18 18" fill="none" stroke="#444" stroke-width="1.5"><rect x="2.5" y="1.5" width="13" height="15" rx="1.5"/><path d="M5.5 6h7M5.5 9h7M5.5 12h7"/></svg>ETF PAIRS</div>
    <div class="tab"><svg viewBox="0 0 18 18" fill="#444"><path d="M5 3l7-2v16l-7-2z"/></svg>FACTORS</div>
  </nav>

  <section class="filters">
    <div class="filter-row"><span class="filter-name">Quality</span><span class="filter-key">Threshold:</span><span class="filter-input">-10</span></div>
    <div class="filter-row"><span class="filter-name"><b>Abs.</b> Stat</span><span class="filter-key">Threshold:</span><span class="filter-input">-10</span></div>
  </section>

  <div class="export">
    <svg viewBox="0 0 24 22" fill="none" stroke="currentColor" stroke-width="2.2"><path d="M11 4H4a2 2 0 0 0-2 2v12a2 2 0 0 0 2 2h13a2 2 0 0 0 2-2v-6"/><path d="M9 14c1-5 5-8 11-8M16 2l4 4-4 4"/></svg>Export
  </div>

  <table class="models-table">
    <colgroup>
      <col style="width:92px"><col style="width:102px"><col style="width:106px"><col style="width:106px">
      <col style="width:83px"><col style="width:83px"><col style="width:83px"><col style="width:83px">
      <col style="width:83px"><col style="width:83px"><col style="width:83px"><col style="width:83px">
    </colgroup>
    <thead>
      <tr><th>ID<svg viewBox="0 0 10 7" fill="none" stroke="#fff" stroke-width="2"><path d="M1 1l4 4 4-4"/></svg></th><th>Sector</th><th>Time</th><th>Quality</th><th>Stat 1</th><th>Stat 2</th><th>Stat 3</th><th>Stat 4</th><th>Stat 5</th><th>Stat 6</th><th>Stat 7</th><th>Stat 8</th></tr>
    </thead>
    <tbody>
      <tr><td class="id">Model 1</td><td>Materials</td><td class="time">2019-07-03<br>12:15:00.000</td><td class="quality">30.2288</td><td>2.01574</td><td>23.305</td><td>-0.149368</td><td>22.3054</td><td>4.63714</td><td>0.945706</td><td>2.81949</td><td>2.60858</td></tr>
      <tr><td class="id">Model 2</td><td>Industrials</td><td class="time">2019-07-03<br>12:15:00.000</td><td class="quality">32.8694</td><td>0.87307</td><td>32.185</td><td>-0.033692</td><td>33.9911</td><td>11.5693</td><td>-0.472968</td><td>-0.830458</td><td>6.80646</td></tr>
      <tr><td class="id">Model 3</td><td>Consumer<br>Discretionary</td><td class="time">2019-07-03<br>12:15:00.000</td><td class="quality">1.66002</td><td>-0.569222</td><td>159.814</td><td>0.0252328</td><td>172.616</td><td>10.2875</td><td>-0.750396</td><td>-0.385309</td><td>4.69146</td></tr>
      <tr><td class="id">Model 4</td><td>Information<br>Technology</td><td class="time">2019-07-03<br>12:15:00.000</td><td class="quality">45.6856</td><td>0.412148</td><td>202.488</td><td>0.0084923</td><td>205.834</td><td>11.9094</td><td>-0.137913</td><td>0.449595</td><td>3.85106</td></tr>
      <tr><td class="id">Model 5</td><td>Information<br>Technology</td><td class="time">2019-07-03<br>12:15:00.000</td><td class="quality">75.7733</td><td>7.06728</td><td>188.605</td><td>0.016913</td><td>161.665</td><td>3.82241</td><td>0.981019</td><td>1.29847</td><td>3.34927</td></tr>
    </tbody>
  </table>
</div>
</body>
</html>
```